Local Flower Farm Needs Business Card Design

I need business cards designed for a flower farm based in Eudora, Kansas.
Business Info:
We are a local cut flower farm located in Eudora, Kansas, founded by Corinne Haldwick. What started as a passion for agriculture and search for more joy in daily life has blossomed into a small business dedicated to providing the community with beautiful, fresh, and sustainable flowers. We specialize in local, seasonal blooms, ensuring that every petal reflects the care and dedication we pour into our craft. Our mission is to deliver the highest quality flowers directly to our customers through local farmers markets and to florists who share our commitment to sustainability. Join us in celebrating the beauty of nature, one bloom at a time!
Contact Details:
Corinne Haldwick
Owner
Phone 913-555-0147
Facebook: Rosalind Thorpe Gardens
Instagram: @RosalindThorpeGardens
Website: RosalindThorpeGardens.example
Target Market(s)
Wholesale to Florists and Direct to Consumer via Farmers Market
Industry/Entity Type
Florist, Farm
Contact Information for Business Card
Name, Contact Info, Logo
Look and feel
Each slider illustrates characteristics of the customer's brand and the style your logo design should communicate.

```html
<!DOCTYPE html>
<html lang="en">
<head>
<meta charset="utf-8">
<title>Rosalind Thorpe Gardens – Business Card</title>
<link href="https://fonts.googleapis.com/css2?family=Montserrat:wght@400;500;700&display=swap" rel="stylesheet">
<style>
  :root {
    --backdrop: #9d9d9d;
    --card-white: #ffffff;
    --ink: #0b262b;
    --deep-teal: #09282d;
    --teal-relief: #1d5a61;
    --ring-grey: #7f8a8c;
  }
  * { box-sizing: border-box; margin: 0; padding: 0; }
  html, body { width: 1093px; height: 1200px; overflow: hidden; }
  body {
    background: var(--backdrop);
    font-family: "Montserrat", sans-serif;
    color: var(--ink);
    position: relative;
  }
  .card {
    position: absolute;
    left: 265px;
    width: 597px;
    border-radius: 20px;
    overflow: hidden;
  }
  .card--front { top: 225px; height: 363px; background: var(--card-white); }
  .card--back  { top: 615px; height: 368px; background: var(--deep-teal); }

  .holder { position: absolute; left: 30px; top: 42px; }
  .holder__name { font-weight: 700; font-size: 24px; line-height: 1.1; letter-spacing: 0.2px; }
  .holder__role { font-weight: 400; font-size: 14px; margin-top: 2px; }

  .brand-seal {
    position: absolute;
    left: 425px; top: 33px;
    width: 128px; height: 128px;
    border: 1px solid var(--ring-grey);
    border-radius: 50%;
    display: flex; align-items: center; justify-content: center;
    text-align: center;
  }
  .brand-seal__name {
    font-weight: 700; font-size: 14px; line-height: 1.25;
    color: var(--ink); width: 96px;
  }

  .contact-list { position: absolute; left: 30px; top: 252px; list-style: none; }
  .contact-list li {
    display: flex; align-items: center;
    font-size: 14px; height: 21.5px;
  }
  .contact-list svg, .contact-list .dot { width: 13px; height: 13px; margin-right: 7px; flex: none; }
  .contact-list .dot { border-radius: 50%; background: var(--ink); }

  .address { position: absolute; left: 405px; top: 302px; font-size: 14px; line-height: 1.2; }

  .back-seal {
    position: absolute;
    left: 162px; top: 54px;
    width: 274px; height: 274px;
    border: 1.5px solid var(--teal-relief);
    border-radius: 50%;
    display: flex; align-items: center; justify-content: center;
    text-align: center;
  }
  .back-seal__name {
    font-weight: 700; font-size: 30px; line-height: 1.2;
    color: var(--teal-relief); width: 210px;
  }
</style>
</head>
<body>
  <section class="card card--front">
    <div class="holder">
      <p class="holder__name">Corinne Haldwick</p>
      <p class="holder__role">Owner</p>
    </div>

    <div class="brand-seal">
      <p class="brand-seal__name">Rosalind Thorpe Gardens</p>
    </div>

    <ul class="contact-list">
      <li>
        <svg viewBox="0 0 24 24" aria-hidden="true"><path fill="#0b262b" d="M6.6 10.8a15 15 0 0 0 6.6 6.6l2.2-2.2c.3-.3.7-.4 1-.2 1.1.4 2.3.6 3.6.6.6 0 1 .4 1 1V20c0 .6-.4 1-1 1A17 17 0 0 1 3 4c0-.6.4-1 1-1h3.5c.6 0 1 .4 1 1 0 1.3.2 2.5.6 3.6.1.3 0 .7-.2 1z"/></svg>
        913-555-0147
      </li>
      <li><span class="dot"></span>Rosalind Thorpe Gardens</li>
      <li><span class="dot"></span>@RosalindThorpeGardens</li>
      <li>
        <svg viewBox="0 0 24 24" aria-hidden="true"><circle cx="12" cy="12" r="10" fill="none" stroke="#0b262b" stroke-width="2"/><ellipse cx="12" cy="12" rx="4" ry="10" fill="none" stroke="#0b262b" stroke-width="1.6"/><path d="M2 12h20" stroke="#0b262b" stroke-width="1.6"/></svg>
        www.RosalindThorpeGardens.example
      </li>
    </ul>

    <address class="address" style="font-style:normal">
      418 Meadowlark Ln, #12<br>
      Eudora, KS 66025
    </address>
  </section>

  <section class="card card--back">
    <div class="back-seal">
      <p class="back-seal__name">Rosalind Thorpe Gardens</p>
    </div>
  </section>
</body>
</html>
```